Hardcore nerd needs to stand out in a sea of dull Defence business cards

Wombarra Devices is a new Australian consulting engineering company that turns research and theory into practical systems. No evangelistic fluff, just mathematics and physics into electronic and optical circuits for consumer products, scientific research or Defence applications.

We already have a recognised logo (provided) which is often dark blue/black on a light background but we're open to other combinations. (Us engineers tend to have limited aesthetic imagination :)

Some of our recent products have included:
* Instrumentation for electrical testing,
* Radar jammers,
* GPS antenna design,
* Satellite tracking systems,
* High power lasers

We're open to both single and double-sided designs - happy to be convinced either way.

P.S. Another group is working on the web page, so - alas - our web site is currently of no use for images/ideas...

Target Market(s)

Engineering managers,
Scientists

Contact Information for Business Card

Dr Colin Harte
R&D Engineer

colin@wombarradevices.com.au
0427 563 710

PO Box XXX (to be confirmed)
Kelsby ACT 2917
Australia

Font styles to use
Serif
Sans Serif

Colors

Designer to choose colors to be used in the design.

Requirements
Must have
• My contact details!
• I've had many (great) "bold and plain" designs submitted already, so feel free to be artistically creative :)
• Happy to take advice re fonts/colours/printability etc.
Nice to have
• I'm not sure if "lists" are more at home on a CV than a business card, but representative services include:
• Applied electromagnetics
• RF and high speed electronics
• Signal and image processing
• Electro-optical and laser systems
• Concept-to-prototype design services
• If you're considering double sided cards, then often measuring/alignment grids/rulers feature on the back of similar cards.
• e.g. https://www.veltranoptics.example/newgrouppage9.cfm?objectgroup_id=4183
• https://www.veltranoptics.example/newgrouppage9.cfm?objectgroup_ID=4185
• ..or even a "Smith chart" (google will return lots)
• Generic images to represent a capability might work - googling images associated with keyword for each of these areas might help:
• - "passive radar", "phased array", "fdtd", "vircator"
• RF and high speed electronic design
• - "smith chart", "microstrip circuits", "dimensioned drawing", "electronic schematic"
• - "dft", "iir filter"
• - "optical cavity". "laser energy level diagram"
• Background/watermarked images outlines/wireframes/schematics would probably look OK.
Should not have
• If a list of projects/services is provided, it is important not to make the client feel that this is "all" the company can do. Engineering design is a creative discipline (like graphics :)
• Please, no stock "military" snaps like planes, missiles, etc!

```html
<!DOCTYPE html>
<html lang="en">
<head>
<meta charset="utf-8">
<title>Wombarra Devices – Business Card</title>
<link rel="stylesheet" href="https://fonts.googleapis.com/css2?family=Lato:wght@400;700;900&display=swap">
<style>
  :root {
    --page: #3a3b3e;
    --card: #050505;
    --pattern: #1b1b1c;
    --white: #ffffff;
    --muted: #8c8c8c;
    --accent: #283a86;
  }
  * { box-sizing: border-box; margin: 0; padding: 0; }
  html, body { width: 1200px; height: 900px; overflow: hidden; }
  body {
    background: var(--page);
    font-family: "Lato", Arial, sans-serif;
    display: flex;
    align-items: center;
    justify-content: center;
    gap: 40px;
  }
  .card {
    position: relative;
    width: 540px;
    height: 310px;
    border-radius: 22px;
    background: var(--card);
    overflow: hidden;
    color: var(--white);
  }

  /* Back: products */
  .products-pattern {
    position: absolute; inset: 0;
    background: radial-gradient(circle at 40% 50%, var(--pattern), var(--card) 90%);
  }
  .name-band {
    position: absolute; top: 0; right: 0; bottom: 0;
    width: 150px;
    background: var(--white);
    display: flex; align-items: center; justify-content: center;
  }
  .band-logotype {
    writing-mode: vertical-rl;
    color: var(--card);
    font-weight: 900;
    font-size: 30px;
    line-height: 1.05;
    letter-spacing: 2px;
    text-transform: uppercase;
    text-align: center;
  }
  .products {
    position: absolute; left: 34px; top: 92px;
  }
  .products-title {
    font-weight: 900;
    font-size: 24px;
    margin-bottom: 12px;
  }
  .products-list { list-style: none; }
  .products-list li {
    display: flex; align-items: center; gap: 10px;
    font-size: 16px;
    line-height: 26px;
  }
  .products-list li::before {
    content: "";
    width: 9px; height: 9px;
    border-radius: 50%;
    background: var(--white);
    flex: none;
  }

  /* Front: contact */
  .logotype {
    position: absolute; left: 40px; top: 70px;
    font-weight: 900;
    font-size: 30px;
    line-height: 1.05;
    letter-spacing: 1px;
    text-transform: uppercase;
    color: var(--white);
  }
  .person {
    position: absolute; right: 52px; top: 112px;
    text-align: right;
  }
  .person-name { font-weight: 900; font-size: 26px; }
  .person-role { font-size: 14px; color: var(--muted); margin-top: 2px; }
  .accent-bar {
    position: absolute; right: 0; top: 108px;
    width: 22px; height: 44px;
    background: var(--accent);
  }
  .address {
    position: absolute; left: 40px; top: 186px;
    font-size: 14px; line-height: 19px; color: var(--muted);
  }
  .contact-list {
    position: absolute; left: 40px; top: 232px;
    list-style: none;
  }
  .contact-list li {
    display: flex; align-items: center; gap: 12px;
    font-size: 14px; line-height: 22px; color: var(--muted);
  }
  .contact-icon { width: 14px; height: 14px; flex: none; }
</style>
</head>
<body>

  <section class="card card-back">
    <div class="products-pattern" role="img" aria-label="Faint repeating brand-mark pattern across the card background"></div>
    <div class="products">
      <h2 class="products-title">PRODUCTS:</h2>
      <ul class="products-list">
        <li>Instrumentation for electrical testing</li>
        <li>Radar jammers</li>
        <li>GPS antenna design</li>
        <li>Satellite tracking systems</li>
        <li>High power lasers</li>
      </ul>
    </div>
    <div class="name-band">
      <p class="band-logotype">Wombarra<br>Devices</p>
    </div>
  </section>

  <section class="card card-front">
    <p class="logotype">Wombarra<br>Devices</p>
    <div class="person">
      <p class="person-name">Dr Colin Harte</p>
      <p class="person-role">R&amp;D Engineer</p>
    </div>
    <span class="accent-bar"></span>
    <p class="address">PO Box XXX<br>Kelsby ACT 2917, Australia</p>
    <ul class="contact-list">
      <li>
        <svg class="contact-icon" viewBox="0 0 16 16" aria-hidden="true"><path fill="#fff" d="M3.5 1l2.5 3-1.5 1.8c.8 1.9 2.2 3.3 4.2 4.2L10.5 8.5l3 2.5-1.5 3C6.5 14 2 9.5 2 2.5z"/></svg>
        0427 563 710
      </li>
      <li>
        <svg class="contact-icon" viewBox="0 0 16 16" aria-hidden="true"><rect x="1" y="3" width="14" height="10" fill="none" stroke="#fff" stroke-width="1.5"/><path d="M1 3l7 6 7-6" fill="none" stroke="#fff" stroke-width="1.5"/></svg>
        colin@wombarradevices.com.au
      </li>
      <li>
        <svg class="contact-icon" viewBox="0 0 16 16" aria-hidden="true"><circle cx="8" cy="8" r="6.5" fill="none" stroke="#fff" stroke-width="1.4"/><ellipse cx="8" cy="8" rx="2.8" ry="6.5" fill="none" stroke="#fff" stroke-width="1.2"/><path d="M1.5 8h13M2.5 5h11M2.5 11h11" stroke="#fff" stroke-width="1"/></svg>
        www.wombarradevices.com.au
      </li>
    </ul>
  </section>

</body>
</html>
```